Corvel Capital LLC

Need Professional Business cards for New Investment Fund

Target Market(s)

High Quality investors

Industry/Entity Type

Financial

Contact Information for Business Card

Phone Number +1 555 284 6190
Name Lukas Varenko
Title Fund Manager
email lv@FundCorvel.com
Website www.FundCorvel.com

Colors

Designer to choose colors to be used in the design.

Requirements
Must have
• Must have our Logo and all of the above. Must be made so lettering and loge can be raised

```html
<!DOCTYPE html>
<html lang="en">
<head>
<meta charset="utf-8">
<title>Corvel Capital – Business Card</title>
<link href="https://fonts.googleapis.com/css2?family=Open+Sans:wght@400;600;700&display=swap" rel="stylesheet">
<style>
  :root {
    --bg: #e6e4e1;
    --card-dark: #16191b;
    --green: #35e831;
    --green-deep: #1f7d1c;
    --band-grey: #434a41;
    --ink: #111411;
  }
  * { box-sizing: border-box; margin: 0; padding: 0; }
  html, body { width: 1200px; height: 864px; overflow: hidden; }
  body {
    background: var(--bg);
    font-family: "Open Sans", Arial, sans-serif;
    position: relative;
  }
  .card {
    position: absolute;
    top: 272px;
    width: 560px;
    height: 320px;
    border-radius: 4px;
    overflow: hidden;
    box-shadow: 0 6px 18px rgba(0,0,0,0.18);
  }
  .card--back { left: 20px; background: var(--card-dark); }
  .card--front { left: 620px; background: var(--card-dark); }

  .wordmark {
    position: absolute;
    font-weight: 700;
    font-size: 30px;
    letter-spacing: 1px;
    display: flex;
    align-items: center;
    gap: 12px;
  }
  .wordmark__dot { width: 14px; height: 14px; border-radius: 50%; }
  .card--back .wordmark {
    left: 0; right: 0; top: 0; bottom: 0;
    justify-content: center;
    color: var(--green-deep);
  }
  .card--back .wordmark__dot { background: var(--green-deep); }

  .front__panel {
    position: absolute; left: 0; top: 0; bottom: 0;
    width: 290px;
    background: var(--green);
    padding: 62px 0 0 34px;
    color: var(--ink);
  }
  .band { position: absolute; top: 0; bottom: 0; }
  .band--grey { left: 290px; width: 20px; background: var(--band-grey); }
  .band--green { left: 310px; width: 16px; background: var(--green); }

  .person__name { font-weight: 700; font-size: 19px; text-transform: uppercase; letter-spacing: 0.3px; }
  .person__title { font-weight: 600; font-size: 14px; margin-top: 2px; }
  .contacts { list-style: none; margin-top: 20px; }
  .contacts li { display: flex; align-items: center; gap: 8px; font-size: 14px; line-height: 21px; }
  .contacts svg { width: 12px; height: 12px; fill: var(--ink); flex: none; }

  .card--front .wordmark {
    left: 326px; right: 0; top: 0; bottom: 0;
    justify-content: center;
    font-size: 24px;
    color: var(--green);
  }
  .card--front .wordmark__dot { background: var(--green); }
</style>
</head>
<body>
  <section class="card card--back" aria-label="Card back">
    <div class="wordmark"><span class="wordmark__dot"></span>Corvel Capital</div>
  </section>

  <section class="card card--front" aria-label="Card front">
    <div class="front__panel">
      <p class="person__name">Lukas Varenko</p>
      <p class="person__title">Fund Manager</p>
      <ul class="contacts">
        <li><svg viewBox="0 0 12 12" aria-hidden="true"><path d="M2.5 1h2l1 3-1.3 1a6 6 0 0 0 2.8 2.8l1-1.3 3 1v2A1.5 1.5 0 0 1 9.5 11 8.5 8.5 0 0 1 1 2.5 1.5 1.5 0 0 1 2.5 1z"/></svg>+1 555 284 6190</li>
        <li><svg viewBox="0 0 12 12" aria-hidden="true"><path d="M1 2.5h10v7H1z M1 2.5l5 4 5-4" stroke="#35e831" stroke-width="0.8"/></svg>lv@FundCorvel.com</li>
        <li><svg viewBox="0 0 12 12" aria-hidden="true"><circle cx="6" cy="6" r="5.5"/></svg>www.FundCorvel.com</li>
      </ul>
    </div>
    <div class="band band--grey"></div>
    <div class="band band--green"></div>
    <div class="wordmark"><span class="wordmark__dot"></span>Corvel Capital</div>
  </section>
</body>
</html>
```